House-share and Room Rental Website (With Focus on the Bedroom Landing Page)

Looking for website design for our House-share (executive accommodation) and room rental business.

Our company name is: Lodgivo could also be written as LodGivo or lodgivo. Either is fine .. just looking for a nice clean catchy logo to go with the design.

EXAMPLES
These are examples of other websites in this field that are doing well. this is a kind of baseline.
https://nestpartners-example.com.au/
https://www.bunkora-example.com/
https://www.dwelzy-example.com/
https://www.habiquo-example.net/
https://www.cohabiscout-example.com.au/

Our business model is to rent rooms to people looking for high-quality accommodation. We fill the gap between those looking to rent rooms and those with rooms to rent. However, our model is slightly different from those already on the market as we looking to fill a massive gap in the market delivering upmarket rooms for rent.(Executive Accommodation) also in the back end will be coupled with a self management process in the back end.

We offer executive style accommodation that stands out above the rest. With special extras like fire safety.. and management processes that create happier homes. We are looking for a web design package that can help us grow and scale our business. We need a design that is captivating

Our MAIN focus is having a room landing page that stands out from the rest... The core of our business will rely on the promotion of the rooms in a share house... so the whole design relies on the BEDROOM landing page to drive results.

Target Market(s)

We have 2 markets we are aiming at ... the first market is people offering rooms to rent who want the highest rental return. The second market is people looking to rent safe, high-quality rooms, in houses that are well managed and looked after.

Industry/Entity Type

Share Economy

Logo Text

LodGivo

Number of Pages Required

5+ page

Font styles to use
Sans Serif

Colors
3276b5

Requirements
Must have
• A messaging system whereby we can create direct communication between those offering rooms and those looking for rooms.
• A call to action that says " Schedule an Inspection"
• Landing page for promoting rooms
• A home page for showing stock.
• Profile page for those selling rooms
• Profile page for those looking for rooms.
• A scheduling calendar for booking inspections
Nice to have
• Pages where new residents can lock in a room.. pay bond and rents.. and sign contracts
• Notifications
• SMS capabilities in the backend.
Should not have
• No script or handwriting fonts.

```html
<!DOCTYPE html>
<html lang="en">
<head>
<meta charset="utf-8">
<title>Lodgivo – Master Bedroom</title>
<link rel="stylesheet" href="https://fonts.googleapis.com/css2?family=Josefin+Sans:wght@300;400;600;700&family=Montserrat:wght@400;600;700&display=swap">
<style>
:root{
  --blue:#3276b5;
  --blue-dark:#2a66a0;
  --ink:#2b2b2b;
  --text:#555;
  --muted:#8a8a8a;
  --line:#d9d9d9;
  --footer:#2b2b2b;
  --footer-bottom:#222;
  --footer-text:#9a9a9a;
  --white:#fff;
}
*{box-sizing:border-box;margin:0;padding:0}
html,body{width:1200px;height:3333px;overflow:hidden}
body{position:relative;background:var(--white);font-family:"Josefin Sans",sans-serif;color:var(--text)}
.abs{position:absolute}
/* top bar */
.topbar{top:0;left:0;width:1200px;height:40px;background:#fff;font-family:"Montserrat",sans-serif;font-size:12px;color:var(--blue)}
.topbar .contact{position:absolute;top:13px;left:100px;display:flex;gap:46px}
.topbar .contact span{display:flex;align-items:center;gap:8px}
.topbar .social{position:absolute;top:12px;right:130px;display:flex;gap:44px}
.dot{width:14px;height:14px;border-radius:50%;background:var(--blue);display:inline-block}
/* nav */
.nav{top:40px;left:0;width:1200px;height:71px;background:var(--blue);color:#fff}
.brand{position:absolute;left:110px;top:18px;display:flex;align-items:center;gap:14px;font-family:"Montserrat",sans-serif;font-weight:700;font-size:24px;letter-spacing:.5px}
.brand .mark{width:36px;height:36px;border-radius:50%;background:#fff}
.menu{position:absolute;right:110px;top:28px;display:flex;gap:30px;font-family:"Montserrat",sans-serif;font-weight:600;font-size:11.5px}
/* hero */
.hero{top:111px;left:0;width:1200px;height:500px;background:linear-gradient(120deg,#6e5a4c 0%,#b89478 30%,#d9c3a8 50%,#7b8a9c 75%,#3e4d63 100%)}
.thumbs{top:633px;left:0;width:1200px;height:127px}
.thumb{position:absolute;top:0;width:149px;height:120px}
.arrow-btn{position:absolute;top:45px;width:30px;height:30px;border:2px solid var(--blue);border-radius:50%}
/* overview */
h2.section{font-weight:600;color:var(--ink);font-size:34px;letter-spacing:.5px}
.overview-title{top:835px;left:104px}
.overview-title::after{content:"";display:block;width:183px;height:2px;background:var(--ink);margin-top:8px}
.overview-text{top:910px;left:104px;width:420px;font-size:18px;line-height:44.5px;color:#666}
.features{top:1254px;left:104px;list-style:none;font-size:18px;color:#666}
.features li{height:44.5px;display:flex;align-items:center;gap:14px}
.features b{color:var(--ink);font-weight:600}
.divider{top:822px;left:600px;width:1px;height:1000px;background:var(--line)}
.room-name{top:834px;left:678px;color:var(--blue);font-size:30px;font-weight:600}
.address{top:890px;left:678px;font-size:27px;line-height:36px;color:var(--muted)}
.utilities{top:1000px;left:681px;font-size:24px;color:#555}
.utilities b{color:var(--ink);font-weight:600}
.price{top:1068px;left:674px;font-size:19px;color:#666;display:flex;align-items:baseline;gap:10px}
.price strong{font-size:42px;font-weight:700;color:var(--blue)}
.price-rule{top:1149px;left:678px;width:426px;height:2px;background:#ccc}
.btn{position:absolute;top:1193px;height:57px;display:flex;align-items:center;justify-content:space-between;padding:0 20px;font-size:21px;font-weight:600}
.btn-gallery{left:680px;width:190px;border:3px solid var(--blue);color:var(--ink)}
.btn-video{left:904px;width:191px;background:var(--blue);color:#fff}
.calendar{top:1333px;left:700px;width:318px;height:250px;background:#fff;box-shadow:0 8px 24px rgba(0,0,0,.15);padding:26px 22px;font-family:"Montserrat",sans-serif}
.cal-grid{display:grid;grid-template-columns:repeat(7,1fr);row-gap:16px;text-align:center;font-size:11px;color:#888}
.cal-grid .hd{font-size:8px;color:#bbb}
.cal-grid .hd.sat{color:#d55}
.cal-grid .mark{position:relative}
.cal-grid .mark::after{content:"";position:absolute;left:50%;bottom:-6px;width:3px;height:3px;margin-left:-1.5px;border-radius:50%;background:#e05555}
.cal-grid .sel{justify-self:center;width:26px;height:26px;margin-top:-6px;line-height:26px;border-radius:50%;background:var(--blue);color:#fff;font-weight:700}
.transport-title{top:1604px;left:682px;font-size:25px;font-weight:600;color:#444}
.transport-icons{top:1720px;left:684px;display:flex;gap:34px}
.distance{top:1806px;left:684px;font-size:23px;color:#555}
.distance b{color:var(--ink);font-weight:600}
/* amenities */
.center-title{left:0;width:1200px;text-align:center}
.center-title::after{content:"";display:block;width:180px;height:2px;background:var(--blue);margin:10px auto 0}
.amenities{top:2050px;left:0;width:1200px;height:180px}
.amenity{position:absolute;top:0;width:160px;margin-left:-80px;text-align:center;font-size:19px;line-height:36px;color:#333}
.amenity svg{display:block;margin:0 auto 34px}
/* map */
.map{top:2427px;left:0;width:1200px;height:380px;background:linear-gradient(135deg,#c7dfb3 0%,#e9e4d8 30%,#eee9dd 55%,#7eb0ec 75%,#e8e3d6 100%)}
.tweet{top:2807px;left:0;width:1200px;height:93px;background:var(--blue);color:#fff;font-family:"Montserrat",sans-serif;font-size:12.5px;text-align:center;line-height:30px;padding-top:16px}
.tweet .bird{position:absolute;left:198px;top:30px;width:32px;height:32px;border-radius:50%;background:#fff}
/* footer */
.footer{top:2900px;left:0;width:1200px;height:378px;background:var(--footer);font-family:"Montserrat",sans-serif;color:var(--footer-text);font-size:10px}
.fcol{position:absolute;top:72px}
.fcol h4{color:#fff;font-size:11px;font-weight:700;letter-spacing:.5px;margin-bottom:24px}
.news{display:flex;gap:16px;margin-bottom:28px}
.news .pic{width:54px;height:54px;background:linear-gradient(135deg,#8fa9c2,#d6dee6)}
.news p{color:#fff;font-weight:600;font-size:10.5px;line-height:15px;width:160px}
.news small{display:block;color:#888;font-size:8px;margin-top:6px;font-weight:400}
.links{display:grid;grid-template-columns:132px 110px;row-gap:17px}
.links .on{color:#fff;font-weight:600}
.subscribe{display:flex;margin:22px 0 10px}
.subscribe span{width:186px;height:28px;background:#fff;color:#aaa;padding:8px 10px;font-size:9px}
.subscribe i{width:30px;height:28px;background:var(--blue)}
.social-row{display:flex;gap:20px;margin-top:36px}
.social-row span{width:18px;height:18px;border-radius:50%;background:#555}
.social-row span.on{border-radius:0;background:var(--blue)}
.about p{line-height:16px;width:210px}
.about .row{display:flex;gap:12px;margin-top:20px;line-height:16px}
.about .row i{width:10px;height:10px;border:1px solid #777;border-radius:50%;margin-top:3px;flex:none}
.bottom{top:3278px;left:0;width:1200px;height:55px;background:var(--footer-bottom);font-family:"Montserrat",sans-serif;font-size:10px;color:#888}
.bottom .copy{position:absolute;left:110px;top:22px}
.bottom .blinks{position:absolute;right:118px;top:22px;display:flex;gap:30px}
</style>
</head>
<body>

<header class="abs topbar">
  <div class="contact">
    <span><svg width="9" height="14" viewBox="0 0 9 14"><rect x="1" y="1" width="7" height="12" rx="1.5" fill="none" stroke="currentColor" stroke-width="1.5"/></svg>2468 - 1357 - 8024</span>
    <span><svg width="14" height="10" viewBox="0 0 14 10"><rect x="0" y="0" width="14" height="10" fill="currentColor"/><path d="M0 0 L7 6 L14 0" stroke="#fff" fill="none"/></svg>support@lodgivo-example.com</span>
  </div>
  <div class="social"><i class="dot"></i><i class="dot"></i><i class="dot"></i></div>
</header>

<nav class="abs nav">
  <div class="brand"><span class="mark"></span>LODGIVO</div>
  <div class="menu">
    <span>HOME</span><span>ABOUT US</span><span>ROOMS</span><span>BOOK NOW</span><span>CONTACT</span>
    <svg width="14" height="14" viewBox="0 0 14 14"><circle cx="6" cy="6" r="4.5" fill="none" stroke="#fff" stroke-width="2"/><path d="M9.5 9.5 L13 13" stroke="#fff" stroke-width="2"/></svg>
  </div>
</nav>

<div class="abs hero" role="img" aria-label="Photo of a warmly lit master bedroom with a large bed and city-view windows"></div>

<div class="abs thumbs">
  <svg class="arrow-btn" style="left:50px" viewBox="0 0 30 30"><path d="M17 9 L11 15 L17 21" fill="none" stroke="#3276b5" stroke-width="2"/></svg>
  <div class="thumb" role="img" aria-label="Bedroom photo" style="left:111px;background:linear-gradient(135deg,#d9cfc2,#8d7a6a)"></div>
  <div class="thumb" role="img" aria-label="Living room photo" style="left:275px;background:linear-gradient(135deg,#c8a57c,#4a3e35)"></div>
  <div class="thumb" role="img" aria-label="Lounge photo" style="left:445px;background:linear-gradient(135deg,#e4ddd2,#5e5046)"></div>
  <div class="thumb" role="img" aria-label="Dining room photo" style="left:611px;background:linear-gradient(135deg,#5d6a6e,#2c3436)"></div>
  <div class="thumb" role="img" aria-label="Sitting room photo" style="left:778px;background:linear-gradient(135deg,#ece6dc,#a99c8a)"></div>
  <div class="thumb" role="img" aria-label="Office space photo" style="left:942px;background:linear-gradient(135deg,#b8c6d6,#3f4f66)"></div>
  <svg class="arrow-btn" style="left:1119px" viewBox="0 0 30 30"><path d="M13 9 L19 15 L13 21" fill="none" stroke="#3276b5" stroke-width="2"/></svg>
</div>

<h2 class="abs section overview-title">OVERVIEW</h2>
<p class="abs overview-text">Sed ut perspiciatis unde omnis iste natus error sit voluptatem accusantium doloremque laudantium, totam rem aperiam, eaque ipsa quae ab illo inven-tore veritatis et quasi architecto beatae vitae dicta sunt explicabo. Nemo enim ipsam voluptatem quia voluptas sit aspernatur aut odit aut fugit, sed quia consequuntur magni dolores eos qui ratione</p>

<ul class="abs features">
  <li><svg width="18" height="18" viewBox="0 0 18 18"><circle cx="9" cy="9" r="7.5" fill="none" stroke="#3276b5" stroke-width="1.4"/><path d="M5 9 L8 12 L13 6" fill="none" stroke="#3276b5" stroke-width="1.6"/></svg>Gender Preference- <b>MALE</b></li>
  <li><svg width="18" height="18" viewBox="0 0 18 18"><circle cx="9" cy="9" r="7.5" fill="none" stroke="#3276b5" stroke-width="1.4"/><path d="M5 9 L8 12 L13 6" fill="none" stroke="#3276b5" stroke-width="1.6"/></svg>Size of room - <b>1000 Sqm</b></li>
  <li><svg width="18" height="18" viewBox="0 0 18 18"><circle cx="9" cy="9" r="7.5" fill="none" stroke="#3276b5" stroke-width="1.4"/><path d="M5 9 L8 12 L13 6" fill="none" stroke="#3276b5" stroke-width="1.6"/></svg>Bathroom - <b>SHARED</b></li>
  <li><svg width="18" height="18" viewBox="0 0 18 18"><circle cx="9" cy="9" r="7.5" fill="none" stroke="#3276b5" stroke-width="1.4"/><path d="M5 9 L8 12 L13 6" fill="none" stroke="#3276b5" stroke-width="1.6"/></svg>Parking - <b>STREET</b></li>
  <li><svg width="18" height="18" viewBox="0 0 18 18"><circle cx="9" cy="9" r="7.5" fill="none" stroke="#3276b5" stroke-width="1.4"/><path d="M5 9 L8 12 L13 6" fill="none" stroke="#3276b5" stroke-width="1.6"/></svg>Smoking - <b>ALLOWED</b></li>
  <li><svg width="18" height="18" viewBox="0 0 18 18"><circle cx="9" cy="9" r="7.5" fill="none" stroke="#3276b5" stroke-width="1.4"/><path d="M5 9 L8 12 L13 6" fill="none" stroke="#3276b5" stroke-width="1.6"/></svg>Minimum contract Year - <b>3 MONTHS</b></li>
  <li><svg width="18" height="18" viewBox="0 0 18 18"><circle cx="9" cy="9" r="7.5" fill="none" stroke="#3276b5" stroke-width="1.4"/><path d="M5 9 L8 12 L13 6" fill="none" stroke="#3276b5" stroke-width="1.6"/></svg>Bed size - <b>45" X 45"</b></li>
  <li><svg width="18" height="18" viewBox="0 0 18 18"><circle cx="9" cy="9" r="7.5" fill="none" stroke="#3276b5" stroke-width="1.4"/><path d="M5 9 L8 12 L13 6" fill="none" stroke="#3276b5" stroke-width="1.6"/></svg>Type of housemates - <b>PROFESSIONALS</b></li>
  <li><svg width="18" height="18" viewBox="0 0 18 18"><circle cx="9" cy="9" r="7.5" fill="none" stroke="#3276b5" stroke-width="1.4"/><path d="M5 9 L8 12 L13 6" fill="none" stroke="#3276b5" stroke-width="1.6"/></svg>Room type - <b>PRIVATE</b></li>
  <li><svg width="18" height="18" viewBox="0 0 18 18"><circle cx="9" cy="9" r="7.5" fill="none" stroke="#3276b5" stroke-width="1.4"/><path d="M5 9 L8 12 L13 6" fill="none" stroke="#3276b5" stroke-width="1.6"/></svg>Internet speed - <b>100 MBPS</b></li>
</ul>

<div class="abs divider"></div>

<h1 class="abs room-name">MASTER BEDROOM</h1>
<p class="abs address">218 Wren Hollow Road<br>Ashby, VA 20190</p>
<p class="abs utilities">Utilites - <b>INCLUDED</b></p>
<p class="abs price">From : <strong>$270</strong> / Night</p>
<div class="abs price-rule"></div>

<div class="btn btn-gallery">GALLERY
  <svg width="34" height="26" viewBox="0 0 34 26"><rect x="1" y="1" width="32" height="24" fill="#bbb"/><path d="M3 22 L12 12 L19 19 L24 14 L31 22Z" fill="#fff"/><circle cx="25" cy="7" r="3" fill="#fff"/></svg>
</div>
<div class="btn btn-video">VIDEO
  <svg width="30" height="30" viewBox="0 0 30 30"><circle cx="15" cy="15" r="13" fill="none" stroke="#fff" stroke-width="2.4"/><path d="M13 9 L19 15 L13 21" fill="none" stroke="#fff" stroke-width="2.4"/></svg>
</div>

<div class="abs calendar">
  <div class="cal-grid">
    <span class="hd">MON</span><span class="hd">TUE</span><span class="hd">WED</span><span class="hd">THU</span><span class="hd">FRI</span><span class="hd sat">SAT</span><span class="hd">SUN</span>
    <span></span><span></span><span>1</span><span>2</span><span>3</span><span>4</span><span>5</span>
    <span>6</span><span>7</span><span class="mark">8</span><span>9</span><span class="mark">10</span><span class="sel">11</span><span>12</span>
    <span>13</span><span class="mark">14</span><span>15</span><span>16</span><span>17</span><span>18</span><span>19</span>
    <span>20</span><span>21</span><span>22</span><span>23</span><span>24</span><span class="mark">25</span><span>26</span>
    <span>27</span><span>28</span>
  </div>
</div>

<h3 class="abs transport-title">TRANSPORT OPTIONS</h3>
<div class="abs transport-icons">
  <svg width="52" height="54" viewBox="0 0 52 54" fill="none" stroke="#444" stroke-width="3"><rect x="6" y="4" width="40" height="40" rx="6"/><path d="M6 26 H46 M6 14 H46"/><circle cx="15" cy="35" r="2.5"/><circle cx="37" cy="35" r="2.5"/><path d="M12 44 V50 M40 44 V50"/></svg>
  <svg width="44" height="54" viewBox="0 0 44 54" fill="none" stroke="#3276b5" stroke-width="3"><rect x="6" y="4" width="32" height="36" rx="6"/><path d="M6 22 H38"/><circle cx="14" cy="31" r="2"/><circle cx="30" cy="31" r="2"/><path d="M12 40 L6 52 M32 40 L38 52 M9 47 H35"/></svg>
  <svg width="50" height="54" viewBox="0 0 50 54" fill="none" stroke="#444" stroke-width="3"><path d="M4 34 V26 L10 14 H40 L46 26 V34 Z M4 26 H46"/><circle cx="13" cy="30" r="2"/><circle cx="37" cy="30" r="2"/><path d="M8 34 V40 M42 34 V40"/></svg>
</div>
<p class="abs distance">Distance to the city &nbsp;- &nbsp;<b>3 KMS</b></p>

<h2 class="abs section center-title" style="top:1938px">ROOM AMENITIES</h2>
<div class="abs amenities">
  <div class="amenity" style="left:118px"><svg width="50" height="62" viewBox="0 0 50 62" fill="none" stroke="#3276b5" stroke-width="2.4"><rect x="12" y="3" width="26" height="24" rx="3"/><rect x="6" y="30" width="38" height="8" rx="2"/><path d="M25 38 V50 M12 56 L25 50 L38 56 M4 22 V34 M46 22 V34"/></svg>Furnished/<br>unfurnished</div>
  <div class="amenity" style="left:278px"><svg width="56" height="62" viewBox="0 0 56 62" fill="none" stroke="#3276b5" stroke-width="2.4"><rect x="3" y="12" width="50" height="32" rx="2"/><path d="M20 52 H36 M28 44 V52"/></svg>TV</div>
  <div class="amenity" style="left:438px"><svg width="46" height="62" viewBox="0 0 46 62" fill="none" stroke="#3276b5" stroke-width="2.4"><rect x="4" y="3" width="38" height="52"/><path d="M23 3 V38 M4 38 H42 M18 20 V26 M28 20 V26 M8 55 V60 M38 55 V60"/></svg>Storage<br>space</div>
  <div class="amenity" style="left:600px"><svg width="66" height="62" viewBox="0 0 66 62" fill="none" stroke="#3276b5" stroke-width="2.4"><rect x="14" y="6" width="26" height="18"/><path d="M22 30 H32 M2 34 H64 M6 34 V58 M60 34 V58"/><rect x="40" y="34" width="20" height="20"/><path d="M44 44 H56"/></svg>Study Desk /<br>Workstation</div>
  <div class="amenity" style="left:758px"><svg width="44" height="62" viewBox="0 0 44 62" fill="none" stroke="#3276b5" stroke-width="2.4"><rect x="4" y="3" width="36" height="54"/><path d="M4 14 H40 M22 14 V57 M10 8 H16 M28 22 V30"/><rect x="8" y="20" width="10" height="32"/></svg>Wardrobe</div>
  <div class="amenity" style="left:918px"><svg width="60" height="62" viewBox="0 0 60 62" fill="none" stroke="#3276b5" stroke-width="2.4"><path d="M50 6 V24 M50 6 H30 M30 6 V12"/><path d="M16 20 Q30 4 44 20 Z"/><path d="M20 28 L18 36 M26 28 L25 38 M32 28 L32 40 M38 28 L40 36"/><rect x="6" y="44" width="48" height="10" rx="2"/></svg>Ensuite shower</div>
  <div class="amenity" style="left:1078px"><svg width="62" height="62" viewBox="0 0 62 62" fill="none" stroke="#3276b5" stroke-width="2.4"><rect x="4" y="30" width="54" height="28"/><path d="M4 40 H58 M31 40 V58"/><circle cx="16" cy="35" r="2"/><circle cx="28" cy="35" r="2"/><path d="M38 12 H56 V26 H38 Z M42 12 V6 M52 12 V6"/></svg>Kitchenette</div>
</div>

<h2 class="abs section center-title" style="top:2314px">OUR LOCATIONS</h2>
<div class="abs map" role="img" aria-label="Street map showing the city harbour and listing locations"></div>

<div class="abs tweet">
  <span class="bird"></span>
  Check out 'Lodgivo - Lorem Ipsum is simply dummy text of the printing and typesetting industry.<br>
  http://lnk.example/Lg7Rq2Vm
</div>

<footer class="abs footer">
  <div class="fcol" style="left:111px">
    <h4>RECENT NEWS</h4>
    <div class="news"><div class="pic" role="img" aria-label="News thumbnail"></div><p>Lorem Ipsum is simply dummy text of the printing<small>Nov 17, 2018</small></p></div>
    <div class="news"><div class="pic" role="img" aria-label="News thumbnail"></div><p>Lorem Ipsum is simply dummy text of the printing<small>Nov 17, 2018</small></p></div>
  </div>
  <div class="fcol" style="left:362px">
    <h4>USEFUL LINKS</h4>
    <div class="links">
      <span>Lodgivo</span><span>Company</span>
      <span>About Firm</span><span>Latest Rooms</span>
      <span class="on">Mobile</span><span>Tenants</span>
      <span>Why us</span><span>Blog Posts</span>
      <span>Social Media</span><span>Help Topics</span>
      <span>Site Map</span><span>Policies</span>
    </div>
  </div>
  <div class="fcol" style="left:611px">
    <h4>MAILING LIST</h4>
    <p style="line-height:16px;width:210px">Sign up for our mailing list to get latest updates and offers.</p>
    <div class="subscribe"><span>Email address</span><i></i></div>
    <p style="font-size:8px;color:#777">We respect your privacy</p>
    <div class="social-row"><span></span><span></span><span class="on"></span><span></span><span></span><span></span></div>
  </div>
  <div class="fcol about" style="left:862px">
    <h4>ABOUT FINANCE</h4>
    <p>Sed ut perspiciatis unde omnis iste natus error sit voluptatem accusantium doloremque laudantium</p>
    <div class="row"><i></i>hello@lodgivo-example.com</div>
    <div class="row"><i></i>P: 2468-7315-902</div>
    <div class="row"><i></i>7/9 Fenmore Lane - Suite 410<br>Harlow Bay - HB 40218</div>
  </div>
</footer>

<div class="abs bottom">
  <span class="copy">© LODGIVO 2018</span>
  <div class="blinks"><span>About</span><span>Services</span><span>Portfolio</span><span>Blog</span><span>Contact</span></div>
</div>

</body>
</html>
```